Banner to be displayed at local Farmers Market Booth.

Graphic Design Brief: Farmers Market Banner Contest

Project Overview:We are seeking talented graphic designers to create a visually appealing banner for our booth at the local farmers market. Our company specializes in healthy, all-natural dog and cat treats, and we want a banner that captures our brand identity while drawing in pet owners who value quality and nutrition for their furry friends.

Banner Specifications:

Size: 24 inches x 60 inches (Horizontal orientation) 24" High X 60 wide

Theme: Vintage/Retro

Style: Warm, inviting, nostalgic with a touch of rustic charm

Colors: Earthy, muted tones such as warm browns, soft greens, and creamy yellows. Pops of red or blue may be used sparingly for accents. OR Black and White with gray scales. Would like to see both

Typography: Retro-style fonts that are readable and align with the vintage aesthetic.

Key Elements to Include: website (www.moltbyfarms.com)

Company Name: Moltby Farms

Tagline: " Simply Honest Bites "
Imagery: Illustrations or stylized graphics of happy dogs and cats, possibly interacting with treats.

Emphasis on Natural Ingredients: Icons or design elements that subtly suggest freshness and quality (e.g., leaves, wheat, bones, or paw prints).

Farmers Market Appeal: A design that blends well with the artisanal, handmade, and farm-fresh atmosphere of the market.

Design Considerations:

The banner should be easily readable from a distance.

A balanced composition that doesn't feel overcrowded.

Should evoke trust and warmth while maintaining a professional look.

Avoid overly modern or sleek elements that don’t align with the vintage aesthetic.

Submission Requirements:

High-resolution digital file in PDF or AI format.

CMYK color mode for printing purposes.

Must include a mockup or preview of how it would look in a real farmers market setting.

We look forward to seeing your creative interpretations of our brand! If you have any questions, feel free to reach out.

Font styles to use
Other font styles liked:
• See attachement

Requirements
Nice to have
• Retro/Vintage,playful BUT NOT whimsical

```html
<!DOCTYPE html>
<html lang="en">
<head>
<meta charset="utf-8">
<title>Moltby Farms – Market Banner</title>
<link rel="stylesheet" href="https://fonts.googleapis.com/css2?family=Russo+One&family=Libre+Baskerville:wght@400;700&display=swap">
<style>
  :root {
    --ink: #0d0d0d;
    --chalk: #f4f4f2;
    --lime: #d9e82c;
    --page: #ffffff;
    --grey-dark: #3a3a3a;
    --grey-light: #d8d8d8;
  }
  html, body {
    margin: 0;
    padding: 0;
    width: 1200px;
    height: 576px;
    overflow: hidden;
    background: var(--page);
  }
  .canvas {
    position: relative;
    width: 1200px;
    height: 576px;
  }
  .banner {
    position: absolute;
    left: 78px;
    top: 58px;
    width: 1078px;
    height: 431px;
    overflow: hidden;
  }
  .banner-backdrop {
    position: absolute;
    inset: 0;
  }
  .brand-name {
    position: absolute;
    left: 28px;
    margin: 0;
    font-family: "Russo One", sans-serif;
    font-weight: 400;
    color: var(--chalk);
    text-transform: uppercase;
    line-height: 1;
    white-space: nowrap;
    opacity: 0.93;
  }
  .brand-name .line {
    display: block;
    font-size: 92px;
    letter-spacing: 6px;
  }
  .brand-name .line-top { margin-top: 36px; transform: scaleY(0.95); }
  .brand-name .line-bottom { margin-top: 6px; transform: scaleY(0.78); transform-origin: top left; }
  .website {
    position: absolute;
    left: 82px;
    top: 226px;
    margin: 0;
    font-family: "Libre Baskerville", serif;
    font-size: 26px;
    letter-spacing: 6px;
    color: var(--chalk);
    text-transform: uppercase;
  }
  .pet-portrait {
    position: absolute;
    left: 653px;
    top: 42px;
    width: 400px;
    height: 282px;
    border-radius: 46% 40% 8% 8% / 40% 36% 6% 6%;
    background: radial-gradient(ellipse at 40% 45%, #e9e9e9 0%, #a8a8a8 45%, #4a4a4a 100%);
    box-shadow: 0 0 0 4px var(--page);
  }
  .stamp {
    position: absolute;
    left: 928px;
    top: 56px;
    display: flex;
    align-items: center;
    gap: 8px;
    font-family: "Libre Baskerville", serif;
    font-size: 24px;
    color: var(--chalk);
  }
  .stamp-dot {
    width: 16px;
    height: 16px;
    border: 2px solid var(--chalk);
    border-radius: 50%;
  }
  .tagline {
    position: absolute;
    left: 32px;
    top: 318px;
    margin: 0;
    font-family: "Libre Baskerville", serif;
    font-weight: 700;
    font-size: 46px;
    letter-spacing: 4px;
    color: var(--ink);
    text-transform: uppercase;
    text-shadow: -2px -2px 0 var(--page);
    white-space: nowrap;
  }
  .service-line {
    position: absolute;
    left: 32px;
    top: 378px;
    margin: 0;
    font-family: "Libre Baskerville", serif;
    font-weight: 700;
    font-size: 33px;
    color: var(--ink);
    text-transform: uppercase;
    white-space: nowrap;
    letter-spacing: -0.3px;
  }
</style>
</head>
<body>
  <div class="canvas">
    <section class="banner">
      <svg class="banner-backdrop" width="1078" height="431" viewBox="0 0 1078 431" aria-hidden="true">
        <defs>
          <radialGradient id="chalkboard" cx="0.45" cy="0.45" r="0.75">
            <stop offset="0" stop-color="#1a1a1a"/>
            <stop offset="0.8" stop-color="#0e0e0e"/>
            <stop offset="1" stop-color="#3a3a3a"/>
          </radialGradient>
        </defs>
        <rect width="1078" height="431" fill="url(#chalkboard)"/>
        <path class="torn-band"
          d="M0 300 L20 296 L40 302 L60 292 L78 290 L98 296 L112 294 L126 306 L150 302 L170 296 L196 298 L214 310 L240 306 L262 316 L290 312 L316 322 L340 318 L360 306 L388 302 L410 294 L434 300 L460 298 L486 310 L510 306 L540 304 L566 314 L600 312 L630 298 L660 304 L690 316 L720 322 L760 330 L800 326 L840 332 L880 324 L920 330 L960 328 L1000 322 L1040 318 L1078 316 L1078 431 L0 431 Z"
          fill="#d9e82c" stroke="#ffffff" stroke-width="5" stroke-linejoin="round"/>
      </svg>

      <h1 class="brand-name">
        <span class="line line-top">Moltby</span>
        <span class="line line-bottom">Farms</span>
      </h1>
      <p class="website">www.moltbyfarms.com</p>

      <div class="pet-portrait" role="img" aria-label="Black and white illustration of a dog and a cat lying side by side"></div>

      <div class="stamp">
        <span class="stamp-dot"></span>
        <span class="stamp-name">Moltby</span>
      </div>

      <p class="tagline">Simply Honest Bites</p>
      <p class="service-line">Purveyors of Premium Pet Food &amp; Treats</p>
    </section>
  </div>
</body>
</html>
```